Book Cover with this title and sub title
Where Auntie Found Her Quiet Orchard
The little book to be smart with your money and help the environment.
Walter P. Brunk Ph. D.
Ellen R. Brunk
Picture below would be on the entire front cover. Words somehow incorporated for easy reading.

```html
<!DOCTYPE html>
<html lang="en">
<head>
<meta charset="utf-8">
<title>Where Auntie Found Her Quiet Orchard</title>
<link href="https://fonts.googleapis.com/css2?family=Bebas+Neue&family=Cinzel:wght@400;500&family=Oswald:wght@500&display=swap" rel="stylesheet">
<style>
  :root {
    --sky-blue: #3a83ec;
    --title-white: #ffffff;
    --honey-gold: #f5b800;
    --petal-bright: #ffe600;
    --petal-yellow: #fbd400;
    --petal-deep: #efb200;
    --pollen-brown: #8a6a2a;
    --leaf-dark: #4a4226;
    --soil-dark: #2e2818;
    --shadow: rgba(0, 0, 0, 0.5);
  }
  * { margin: 0; padding: 0; box-sizing: border-box; }
  html, body { width: 933px; height: 1200px; overflow: hidden; background: #ffffff; }
  .cover {
    position: relative;
    width: 933px;
    height: 1200px;
    overflow: hidden;
    background: var(--sky-blue);
  }
  .title-band {
    position: absolute;
    inset: 0 0 auto 0;
    height: 396px;
    background: var(--sky-blue);
  }
  .cover-photo {
    position: absolute;
    left: 0; top: 396px;
    width: 933px; height: 804px;
    background:
      radial-gradient(ellipse 20% 22% at 38% 42%, rgba(138,106,42,0.75) 0%, rgba(138,106,42,0) 100%),
      radial-gradient(ellipse 14% 12% at 56% 26%, rgba(74,58,30,0.55) 0%, rgba(74,58,30,0) 100%),
      radial-gradient(ellipse 30% 26% at 47% 56%, rgba(239,178,0,0.9) 0%, rgba(239,178,0,0) 100%),
      radial-gradient(ellipse 22% 18% at 100% 0%, rgba(120,96,60,0.8) 0%, rgba(120,96,60,0) 100%),
      radial-gradient(ellipse 24% 26% at 0% 100%, rgba(46,40,24,0.95) 0%, rgba(46,40,24,0) 100%),
      radial-gradient(ellipse 22% 24% at 100% 100%, rgba(46,40,24,0.9) 0%, rgba(46,40,24,0) 100%),
      radial-gradient(ellipse 90% 85% at 50% 45%, var(--petal-bright) 0%, var(--petal-yellow) 45%, var(--petal-deep) 78%, var(--leaf-dark) 100%);
  }
  .title-main {
    position: absolute;
    top: 86px; left: 0; width: 100%;
    text-align: center;
    font-family: "Bebas Neue", "Oswald", sans-serif;
    font-weight: 400;
    font-size: 94px;
    line-height: 1;
    color: var(--title-white);
    letter-spacing: 1px;
  }
  .title-connector {
    position: absolute;
    top: 180px; left: 0; width: 100%;
    text-align: center;
    font-family: "Cinzel", serif;
    font-size: 34px;
    letter-spacing: 10px;
    color: var(--title-white);
  }
  .title-feature {
    position: absolute;
    top: 220px; left: 0; width: 100%;
    text-align: center;
    font-family: "Cinzel", serif;
    font-size: 118px;
    line-height: 1.05;
    letter-spacing: 12px;
    color: var(--honey-gold);
    text-shadow: 4px 6px 8px var(--shadow);
  }
  .subtitle {
    position: absolute;
    top: 351px; left: 0; width: 100%;
    text-align: center;
    font-family: "Oswald", sans-serif;
    font-weight: 500;
    font-size: 30px;
    line-height: 45px;
    color: var(--title-white);
    text-transform: uppercase;
    letter-spacing: -0.5px;
    text-shadow: 2px 3px 5px var(--shadow);
  }
  .subtitle-rule {
    position: absolute;
    top: 395px;
    height: 2px;
    background: var(--title-white);
  }
  .subtitle-rule.left { left: 113px; width: 92px; }
  .subtitle-rule.right { left: 714px; width: 95px; }
  .authors {
    position: absolute;
    top: 1036px; left: 0; width: 100%;
    text-align: center;
    font-family: "Cinzel", serif;
    font-size: 54px;
    line-height: 64px;
    color: var(--title-white);
    text-shadow: 2px 3px 6px var(--shadow);
  }
</style>
</head>
<body>
  <main class="cover">
    <div class="title-band"></div>
    <div class="cover-photo" role="img" aria-label="Close-up photograph of a honeybee gathering pollen on a bright yellow dandelion flower, filling the lower cover"></div>

    <h1 class="title-main">Where Auntie Found</h1>
    <p class="title-connector">HER QUIET</p>
    <p class="title-feature">ORCHARD</p>

    <span class="subtitle-rule left"></span>
    <span class="subtitle-rule right"></span>
    <p class="subtitle">The little book to be smart with your<br>money and help the environment.</p>

    <p class="authors">Walter P. Brunk Ph. D.<br>Ellen R. Brunk</p>
  </main>
</body>
</html>
```